BOLD & MINIMALIST DESIGN NEEDED

We want a very bold but minimalistic business card design that is impactful and utilizes both sides of the business card. Our current logo is included for your use.

We want bold fonts and good use of negative space. We don't want the logo to overpower the design.

Target Market(s)

Professionals who are building new commercial buildings.

Industry/Entity Type

Construction

Contact Information for Business Card

Name, Title, email, office phone, cell phone, website

Font styles to use
Serif
Sans Serif

Requirements
Must have
• Bold design!

```html
<!DOCTYPE html>
<html lang="en">
<head>
<meta charset="utf-8">
<title>Ridgecrest Design + Build — Business Card</title>
<link href="https://fonts.googleapis.com/css2?family=Poppins:wght@400;600;800&display=swap" rel="stylesheet">
<style>
  :root {
    --page: #e9e7e6;
    --card-top: #f6f3f2;
    --card-bottom: #e6e1df;
    --ink: #0b0c0d;
    --green: #8dc63f;
    --green-light: #c6e59a;
    --white: #ffffff;
  }
  * { margin: 0; padding: 0; box-sizing: border-box; }
  html, body { width: 1200px; height: 900px; overflow: hidden; background: var(--page); }
  .card {
    position: absolute; left: 100px; top: 140px; width: 1000px; height: 620px;
    background: linear-gradient(180deg, var(--card-top), var(--card-bottom));
    box-shadow: 0 18px 40px rgba(0,0,0,.18);
    overflow: hidden;
    font-family: "Poppins", sans-serif;
  }
  .card__bands { position: absolute; inset: 0; }
  .brand {
    position: absolute; left: 0; right: 0; top: 150px;
    display: flex; flex-direction: column; align-items: center; gap: 6px;
    color: var(--ink); font-weight: 800;
  }
  .brand__row { display: flex; align-items: center; gap: 18px; }
  .brand__square { width: 40px; height: 40px; background: var(--green); }
  .brand__name { font-size: 64px; line-height: 1; letter-spacing: 1px; }
  .brand__tagline { font-size: 24px; letter-spacing: 10px; }
  .person {
    position: absolute; right: 530px; top: 470px; width: 280px;
    text-align: right; color: var(--green);
    font-size: 31px; font-weight: 600; line-height: 1;
    padding-bottom: 10px; border-bottom: 1.5px solid var(--green);
  }
  .phones { position: absolute; right: 530px; top: 516px; color: var(--white); }
  .contact-line {
    display: flex; align-items: center; gap: 14px;
    font-size: 28px; line-height: 36px; font-weight: 400;
  }
  .phones .contact-line { justify-content: flex-end; }
  .icon { width: 28px; height: 28px; flex: none; }
  .role {
    position: absolute; left: 522px; top: 466px; width: 262px;
    color: var(--ink); font-size: 21px; font-weight: 400;
    padding-bottom: 8px; border-bottom: 1.5px solid var(--ink);
  }
  .online { position: absolute; left: 524px; top: 516px; color: var(--ink); }
  .online .contact-line { font-size: 27px; }
</style>
</head>
<body>
<div class="card">
  <svg class="card__bands" viewBox="0 0 1000 620" width="1000" height="620">
    <defs>
      <linearGradient id="greenFade" x1="0" x2="1" y1="0" y2="0">
        <stop offset="0" stop-color="var(--green)"/>
        <stop offset="0.45" stop-color="var(--green)"/>
        <stop offset="1" stop-color="var(--green-light)"/>
      </linearGradient>
    </defs>
    <polygon class="roof-stripe roof-stripe--dark" points="0,515 496,334 496,342 0,523" fill="var(--ink)"/>
    <polygon class="roof-stripe roof-stripe--green" points="496,334 1000,514 1000,521 496,341" fill="var(--green)"/>
    <polygon class="band band--dark" points="0,532 496,352 496,620 0,620" fill="var(--ink)"/>
    <polygon class="band band--green" points="496,352 1000,530 1000,620 496,620" fill="url(#greenFade)"/>
  </svg>

  <div class="brand">
    <div class="brand__row">
      <span class="brand__square"></span>
      <span class="brand__name">RIDGECREST</span>
    </div>
    <span class="brand__tagline">DESIGN + BUILD</span>
  </div>

  <div class="person">DANIEL HARPER</div>
  <div class="phones">
    <div class="contact-line">021-555 014 372
      <svg class="icon" viewBox="0 0 28 28"><rect x="1" y="1" width="26" height="26" rx="3" fill="none" stroke="var(--green)" stroke-width="1.8"/><path d="M9 7l3 0 1.5 4-2 1.5a9 9 0 0 0 4 4l1.5-2 4 1.5v3a2 2 0 0 1-2 2A13 13 0 0 1 7 9a2 2 0 0 1 2-2z" fill="none" stroke="var(--green)" stroke-width="1.6"/></svg>
    </div>
    <div class="contact-line">021-555 014 388
      <svg class="icon" viewBox="0 0 28 28"><rect x="1" y="1" width="26" height="26" rx="3" fill="none" stroke="var(--green)" stroke-width="1.8"/><rect x="9" y="6" width="10" height="16" rx="1.5" fill="none" stroke="var(--green)" stroke-width="1.6"/><line x1="12.5" y1="19" x2="15.5" y2="19" stroke="var(--green)" stroke-width="1.4"/></svg>
    </div>
  </div>

  <div class="role">MANAGING DIRECTOR</div>
  <div class="online">
    <div class="contact-line">
      <svg class="icon" viewBox="0 0 28 28"><rect x="1" y="1" width="26" height="26" rx="3" fill="none" stroke="var(--ink)" stroke-width="1.8"/><rect x="6" y="8" width="16" height="12" fill="var(--ink)"/><path d="M6 8l8 7 8-7" fill="none" stroke="var(--green)" stroke-width="1.4"/></svg>
      hello@ridgecrestbuild.com
    </div>
    <div class="contact-line">
      <svg class="icon" viewBox="0 0 28 28"><rect x="1" y="1" width="26" height="26" rx="3" fill="none" stroke="var(--ink)" stroke-width="1.8"/><circle cx="14" cy="14" r="8" fill="none" stroke="var(--ink)" stroke-width="1.6"/><ellipse cx="14" cy="14" rx="3.5" ry="8" fill="none" stroke="var(--ink)" stroke-width="1.3"/><line x1="6" y1="14" x2="22" y2="14" stroke="var(--ink)" stroke-width="1.3"/></svg>
      www.ridgecrestbuild.com
    </div>
  </div>
</div>
</body>
</html>
```